Webshop for furniture and lamps

We need a design for a web shop with APP that should have two options:
1-Webshop in general which should attract to private customer in general and
2-Website that is meant to attract big customers as hotels and restaurants who would have their own customerize login.

That's the idea behind the shop.

It should be diveded into 4 parts
vintage furniture
rattan set outdoor and indoor
lamps and
wooden wall decor

The name of the shop is loma vereda!

Please kindly make me an offer.

Reason: Dear designers, so far there hasn't been a design that really matched. Look up German web sites like www.glimmerhof-wohnen.de or www.sitzraum77.de... Haven't been convinced by designs! Sorry folks. Please submit some new ones. Kind regards Ned

```html
<!DOCTYPE html>
<html lang="en">
<head>
<meta charset="utf-8">
<title>loma vereda – Choose your membership</title>
<link rel="stylesheet" href="https://fonts.googleapis.com/css2?family=Open+Sans:wght@400;600;700&display=swap">
<style>
  :root {
    --white: #ffffff;
    --private-tone: #3b2c24;
    --private-deep: #1f1713;
    --private-light: #6a5a52;
    --business-tone: #e29a48;
    --business-deep: #c97a2c;
    --business-light: #f0bd80;
  }
  * { box-sizing: border-box; margin: 0; padding: 0; }
  html, body { width: 1200px; height: 581px; overflow: hidden; }
  body { font-family: "Open Sans", sans-serif; color: var(--white); }

  .membership-page { position: relative; width: 1200px; height: 581px; overflow: hidden; }

  .backdrop { position: absolute; inset: 0; display: flex; }
  .backdrop-half { width: 600px; height: 100%; }
  .backdrop-private {
    background:
      radial-gradient(ellipse 320px 200px at 470px 400px, var(--private-light), transparent 70%),
      linear-gradient(180deg, var(--private-tone) 0%, #33261f 60%, var(--private-deep) 100%);
  }
  .backdrop-business {
    background:
      radial-gradient(ellipse 420px 220px at 250px 400px, var(--business-light), transparent 70%),
      linear-gradient(180deg, var(--business-deep) 0%, var(--business-tone) 45%, #eaa55a 100%);
  }

  .page-heading { position: absolute; top: 66px; left: 0; width: 100%; text-align: center; }
  .page-title { font-size: 46px; font-weight: 700; letter-spacing: 2.5px; line-height: 56px; }
  .page-subtitle { margin-top: 10px; font-size: 22px; font-weight: 700; letter-spacing: 2.2px; line-height: 28px; }

  .membership-option { position: absolute; top: 240px; width: 420px; height: 180px; }
  .membership-option.private { left: 130px; }
  .membership-option.business { left: 730px; }

  .option-icon { position: absolute; left: 0; top: 19px; width: 42px; height: 108px; }
  .option-body { position: absolute; left: 88px; top: 0; width: 300px; }
  .option-title { font-size: 20px; font-weight: 700; line-height: 30px; }
  .option-rule { width: 60px; height: 2px; background: var(--white); margin-top: 6px; }
  .option-text { margin-top: 16px; font-size: 11.5px; line-height: 15.5px; }
  .option-button {
    display: inline-block; margin-top: 30px; margin-left: -1px;
    width: 95px; height: 32px; border: 2px solid var(--white);
    font-size: 9.5px; font-weight: 700; line-height: 28px; text-align: center;
    color: var(--white); text-decoration: none; letter-spacing: 0.3px;
  }

  .signup-note { position: absolute; top: 513px; left: 0; width: 100%; text-align: center; font-size: 16px; line-height: 24px; }
  .signup-note strong { font-weight: 700; }
</style>
</head>
<body>
<main class="membership-page">
  <div class="backdrop" role="img" aria-label="Photograph of a hotel bedroom with a wooden block wall, wall lamps and a made bed, tinted dark on the left and orange on the right">
    <div class="backdrop-half backdrop-private"></div>
    <div class="backdrop-half backdrop-business"></div>
  </div>

  <header class="page-heading">
    <h1 class="page-title">WELCOME VISITORS</h1>
    <p class="page-subtitle">PLEASE CHOOSE YOUR MEMBERSHIP</p>
  </header>

  <section class="membership-option private">
    <svg class="option-icon" viewBox="0 0 42 108" aria-hidden="true">
      <circle cx="21" cy="10" r="10" fill="#fff"/>
      <path d="M6 24 H36 Q42 24 42 30 V66 H34 V108 H8 V66 H0 V30 Q0 24 6 24 Z" fill="#fff"/>
    </svg>
    <div class="option-body">
      <h2 class="option-title">PRIVATE CUSTOMER</h2>
      <div class="option-rule"></div>
      <p class="option-text">Lorem ipsum dolar sit amet voluptatem<br>fugit aut illo omnis explicabo ipsa nemo rem<br>ipsam dolores ut voluptatem doloremque aut<br>perspiciatis beatae magni architecto odit</p>
      <a class="option-button" href="#">LOG IN HERE</a>
    </div>
  </section>

  <section class="membership-option business">
    <svg class="option-icon" viewBox="0 0 42 108" aria-hidden="true">
      <circle cx="21" cy="10" r="10" fill="#fff"/>
      <path d="M6 24 H15 L21 40 L27 24 H36 Q42 24 42 30 V66 H34 V72 H30 L26 108 H16 L12 72 H8 V66 H0 V30 Q0 24 6 24 Z" fill="#fff"/>
      <path d="M17 24 H25 L21 36 Z" fill="#fff"/>
    </svg>
    <div class="option-body">
      <h2 class="option-title">BUSINESS</h2>
      <div class="option-rule"></div>
      <p class="option-text">Lorem ipsum dolar sit amet voluptatem<br>fugit aut illo omnis explicabo ipsa nemo rem<br>ipsam dolores ut voluptatem doloremque aut<br>perspiciatis beatae magni architecto odit</p>
      <a class="option-button" href="#">LOG IN HERE</a>
    </div>
  </section>

  <p class="signup-note">Not member? Please <strong>SIGN UP</strong> here</p>
</main>
</body>
</html>
```